Design some Business Card for shipping company

We need a creative business card designed for a shipping company. All relevant information such as address and phone number can be found on our website. Will need a design for both front and back. The front will container our logo, slogan, contact information etc. The back will have a coupon and some text. check out www.larvintolfreight.example for all the information. We need something memorable and unique that will stand out. It needs to a horizontal design. Not vertical.

```html
<!DOCTYPE html>
<html lang="en">
<head>
<meta charset="utf-8">
<title>Larvintol Freight Business Cards</title>
<link rel="stylesheet" href="https://fonts.googleapis.com/css2?family=Mulish:wght@800&family=Questrial&display=swap">
<style>
  :root{
    --stage:#2b2b2b;
    --paper:#ffffff;
    --green:#1f7a45;
    --green-band:#2f8a55;
    --red:#c8242b;
    --red-band:#c9454b;
    --ink:#1a1a1a;
    --black:#111111;
  }
  *{margin:0;padding:0;box-sizing:border-box}
  html,body{width:1200px;height:780px;overflow:hidden}
  body{background:var(--stage);position:relative;font-family:"Questrial",sans-serif;color:var(--ink)}
  .card{position:absolute;width:560px;height:320px;background:var(--paper);overflow:hidden}
  .card--front{left:30px;top:40px}
  .card--back{left:610px;top:420px}
  .stripes{position:absolute;left:0;top:0;width:560px;height:320px}

  .brand{position:absolute;text-align:center;left:0;right:0}
  .brand__dot{width:70px;height:70px;border-radius:50%;background:var(--green);margin:0 auto 16px}
  .brand__name{font-family:"Mulish",sans-serif;font-weight:800;color:var(--green);font-size:42px;line-height:1}
  .brand__slogan{font-family:"Mulish",sans-serif;font-weight:800;font-size:19px;color:var(--ink);margin-top:6px}
  .card--front .brand{top:42px}

  .web-band{position:absolute;left:150px;top:268px;color:#fff;font-size:13px;font-family:"Mulish",sans-serif;font-weight:800;transform:rotate(-3deg)}

  .card--back .brand{left:auto;right:22px;top:30px;display:flex;align-items:center;gap:10px;text-align:left}
  .card--back .brand__dot{width:40px;height:40px;margin:0}
  .card--back .brand__name{font-size:23px}
  .card--back .brand__slogan{font-size:11px;margin-top:2px}

  .person{position:absolute;left:50px;top:90px}
  .person__name{font-size:24px;color:var(--ink)}
  .person__role{font-size:11px;margin:2px 0 0 42px}

  .contacts{position:absolute;left:42px;top:160px;list-style:none;font-size:11px}
  .contacts li{display:flex;align-items:flex-start;gap:10px;height:21px}
  .contacts svg{width:18px;height:15px;flex:none;fill:var(--red)}

  .coupon-lines{position:absolute;right:26px;top:128px;width:250px}
  .coupon-lines span{display:block;height:2px;background:var(--red);margin-bottom:14px}
</style>
</head>
<body>

<section class="card card--front">
  <svg class="stripes" viewBox="0 0 560 320">
    <polygon points="0,292 70,282 44,320 0,320" fill="var(--black)"/>
    <polygon points="70,282 370,250 350,278 44,320" fill="var(--red-band)"/>
    <polygon points="370,250 560,238 560,260 350,278" fill="var(--green-band)"/>
  </svg>
  <div class="brand">
    <div class="brand__dot"></div>
    <div class="brand__name">Larvintol Freight</div>
    <div class="brand__slogan">Reliable Low-Cost Freight to Nairobi</div>
  </div>
  <div class="web-band">www.larvintolfreight.example</div>
</section>

<section class="card card--back">
  <svg class="stripes" viewBox="0 0 560 320">
    <polygon points="0,300 220,286 190,320 0,320" fill="var(--black)"/>
    <polygon points="220,286 470,262 450,290 190,320" fill="var(--red-band)"/>
    <polygon points="470,262 560,254 560,282 450,290" fill="var(--green-band)"/>
  </svg>
  <div class="brand">
    <div class="brand__dot"></div>
    <div>
      <div class="brand__name">Larvintol Freight</div>
      <div class="brand__slogan">Reliable Low-Cost Freight to Nairobi</div>
    </div>
  </div>
  <div class="person">
    <div class="person__name">Jaren Dole</div>
    <div class="person__role">Director</div>
  </div>
  <ul class="contacts">
    <li><svg viewBox="0 0 18 15"><rect x="4" y="1" width="9" height="13" rx="2"/></svg>USA: +1 555 410 2287</li>
    <li><svg viewBox="0 0 18 15"><rect x="4" y="1" width="9" height="13" rx="2"/></svg>KENYA: +254700118842, 0700118842</li>
    <li><svg viewBox="0 0 18 15"><rect x="1" y="2" width="16" height="11"/><polyline points="1,2 9,9 17,2" fill="none" stroke="#fff" stroke-width="1.5"/></svg>info@larvintolfreight.example</li>
    <li><svg viewBox="0 0 18 15"><circle cx="9" cy="7.5" r="7"/><ellipse cx="9" cy="7.5" rx="3" ry="7" fill="none" stroke="#fff"/><line x1="2" y1="7.5" x2="16" y2="7.5" stroke="#fff"/></svg>www.larvintolfreight.example</li>
    <li><svg viewBox="0 0 18 15"><polygon points="9,1 17,8 15,8 15,14 3,14 3,8 1,8"/></svg>1480 Harbor Crest Ave Ste #36<br>Portview WA 98000</li>
  </ul>
  <div class="coupon-lines"><span></span><span></span><span></span><span></span></div>
</section>

</body>
</html>
```